Need business card with a logo for a hearing aid sales and audiology business. We have two Hearing Instrument Specialists and one Audiologist on staff. Over 25 years in business. Locally owned and operated. Financing available. Most insurances accepted.

Summit Audio Wellness LLC
48730 W Larchmont, Suite 7
Spokane, WA 99281
509-617-2084
www.summitaudiowell.example

Manager
Tobias Kerrell HIS COHC
License #71829046

Target Market(s)

50yr old + people with a hearing loss.

Industry/Entity Type

Business

Contact Information for Business Card

48730 W Larchmont, Suite 7
Spokane, WA 99281
509-617-2084
www.summitaudiowell.example

Manager
Tobias Kerrell HIS COHC
NLVE #71829046

Font styles to use
Serif
Sans Serif

Requirements
Must have
• Business name, Tobias's name and title(s) and contact information, License #, web address

```html
<!DOCTYPE html>
<html lang="en">
<head>
<meta charset="utf-8">
<title>Summit Audio Wellness LLC – Business Card</title>
<link href="https://fonts.googleapis.com/css2?family=Open+Sans:wght@400;600;700&family=Questrial&display=swap" rel="stylesheet">
<style>
  :root {
    --stage: #e9e6e1;
    --card-white: #ffffff;
    --card-black: #262626;
    --brand-red: #e31b23;
    --ink: #1a1a1a;
    --ink-soft: #333333;
  }
  * { margin: 0; padding: 0; box-sizing: border-box; }
  html, body { width: 1200px; height: 900px; overflow: hidden; }
  body {
    background: var(--stage);
    position: relative;
    font-family: "Open Sans", Arial, sans-serif;
  }
  .card {
    position: absolute;
    width: 700px;
    height: 400px;
    overflow: hidden;
    box-shadow: 0 6px 18px rgba(0,0,0,.18);
  }
  .card-back { left: 420px; top: 40px; background: var(--card-black); }
  .card-front { left: 80px; top: 460px; background: var(--card-white); }

  .brand {
    position: absolute;
    display: flex;
    align-items: center;
    gap: 22px;
  }
  .brand-mark { border-radius: 50%; flex: none; }
  .brand-name {
    font-family: "Questrial", Arial, sans-serif;
    font-weight: 400;
    text-transform: uppercase;
    line-height: 1.05;
    letter-spacing: 1px;
  }
  .card-back .brand { left: 110px; top: 130px; }
  .card-back .brand-mark { width: 120px; height: 120px; border: 6px solid #fff; }
  .card-back .brand-name { color: #fff; font-size: 40px; }

  .card-front .brand { left: 372px; top: 150px; }
  .card-front .brand-mark { width: 86px; height: 86px; background: var(--brand-red); }
  .card-front .brand-name { color: var(--brand-red); font-size: 27px; }

  .decor { position: absolute; inset: 0; }

  .holder { position: absolute; left: 76px; top: 28px; }
  .holder-name { color: var(--brand-red); font-weight: 700; font-size: 19px; }
  .holder-title { color: var(--ink-soft); font-size: 14px; margin-top: -3px; }

  .contact {
    position: absolute;
    left: 30px;
    top: 128px;
    color: var(--ink);
    font-size: 15px;
    line-height: 1.35;
  }
  .contact-address { margin-left: 20px; margin-bottom: 8px; }
  .contact-line { display: flex; align-items: center; gap: 8px; }
  .contact-line svg { flex: none; }
  .license { margin-top: 4px; font-weight: 700; color: var(--ink); }
  .license-label { color: var(--brand-red); }
</style>
</head>
<body>

  <section class="card card-back" aria-label="Card back">
    <div class="brand">
      <span class="brand-mark"></span>
      <span class="brand-name">Summit Audio<br>Wellness LLC</span>
    </div>
  </section>

  <section class="card card-front" aria-label="Card front">
    <svg class="decor" width="700" height="400" viewBox="0 0 700 400">
      <polygon points="0,22 64,22 54,58 0,58" fill="var(--brand-red)"/>
      <polygon points="30,58 64,22 64,58" fill="var(--card-black)"/>
      <polygon points="0,318 348,318 334,342 0,342" fill="var(--brand-red)"/>
      <polygon points="356,318 700,318 700,376 330,344" fill="var(--card-black)"/>
    </svg>

    <div class="holder">
      <div class="holder-name">Tobias Kerrell HIS COHC</div>
      <div class="holder-title">Manager</div>
    </div>

    <div class="contact">
      <div class="contact-address">48730 W Larchmont, Suite 7<br>Spokane, WA 99281</div>
      <div class="contact-line">
        <svg width="12" height="12" viewBox="0 0 24 24" aria-hidden="true"><path fill="#e31b23" d="M6.6 10.8a15 15 0 0 0 6.6 6.6l2.2-2.2c.3-.3.7-.4 1-.2 1.1.4 2.3.6 3.6.6.6 0 1 .4 1 1V20c0 .6-.4 1-1 1A17 17 0 0 1 3 4c0-.6.4-1 1-1h3.5c.6 0 1 .4 1 1 0 1.3.2 2.5.6 3.6.1.3 0 .7-.2 1z"/></svg>
        <span>509-617-2084</span>
      </div>
      <div class="contact-line">
        <svg width="12" height="12" viewBox="0 0 24 24" aria-hidden="true"><circle cx="12" cy="12" r="11" fill="#e31b23"/><path d="M3 12h18M12 1c3 3 3 19 0 22M12 1c-3 3-3 19 0 22" stroke="#fff" stroke-width="1.6" fill="none"/></svg>
        <span>www.summitaudiowell.example</span>
      </div>
      <div class="license"><span class="license-label">License</span> #71829046</div>
    </div>

    <div class="brand">
      <span class="brand-mark"></span>
      <span class="brand-name">Summit Audio<br>Wellness LLC</span>
    </div>
  </section>

</body>
</html>
```